Harborview Estates Business Card for Apartment Buildings

Create business cards for resident managers who run apartment buildings. The audience is the public who are searching for apartment rentals, and current residents who live at the apartment building. Key design element will be incorporating the company logo, however, the logo cannot dominate. The building name and manager name are more important than the logo. Current business card design leaves little room for copy, so we may need to reduce the size on the current card to allow for more space for copy.

Target Market(s)

Adults 18-65 years of age, who are looking for an apartment rental, plus current residents who live at our apartment buildings.

Industry/Entity Type

Property Management

Contact Information for Business Card

A major design element will be use of the company logo. Important property and manager contact information must be part of the design. The size of the logo will need to be reduced to make room for building and manager contact copy.

Font styles to use
Sans Serif

Colors
3176b5
000000
959595
ffffff

Requirements
Must have
• 1) Incorporate the company logo.
• 2) Use the company colors (dark blue, black/grey, over white).
• 3) FEATURE THE BUILDING NAME
• 4) FEATURE THE MANAGER NAME
• 5) The company name is less important than BUILDING and MANAGER
• 6) Manager contact information
• **SEE ATTACHED CREATIVE BRIEF**
Nice to have
• 1) Back of card logo watermark
• 2) Ability to write notes on back of carfd
Should not have
• Avoid letting the company logo dominate the card, the building name and manager are more important than the company logo.

```html
<!DOCTYPE html>
<html lang="en">
<head>
<meta charset="utf-8">
<title>Harborview Estates – Business Card</title>
<link rel="stylesheet" href="https://fonts.googleapis.com/css2?family=Oswald:wght@600&family=Work+Sans:wght@400;500;600&display=swap">
<style>
  :root {
    --brand-blue: #3176b5;
    --stage: #141414;
    --grey: #959595;
    --white: #ffffff;
  }
  * { margin: 0; padding: 0; box-sizing: border-box; }
  html, body {
    width: 1200px; height: 900px; overflow: hidden;
    background: var(--stage);
    font-family: "Work Sans", sans-serif;
    color: var(--white);
  }
  .canvas {
    width: 1200px; height: 900px;
    display: flex; flex-direction: column; align-items: center; justify-content: center;
    gap: 28px;
  }
  .card {
    width: 700px; height: 400px;
    background: linear-gradient(135deg, #1f1f1f 0%, #2a2a2a 60%, #333 100%);
    box-shadow: 0 14px 30px rgba(0,0,0,.6);
    position: relative;
    overflow: hidden;
  }
  /* Front */
  .card-front {
    display: flex; flex-direction: column; align-items: center; justify-content: center;
  }
  .brand-lockup { display: flex; align-items: center; gap: 16px; }
  .brand-square { width: 30px; height: 30px; background: var(--brand-blue); }
  .brand-name {
    font-weight: 600; font-size: 34px; letter-spacing: 2px;
    text-transform: uppercase; color: var(--white);
  }
  .front-web { margin-top: 72px; font-size: 18px; letter-spacing: 3px; }
  .web-accent { color: var(--brand-blue); }

  /* Back */
  .card-back {
    display: flex; flex-direction: column; align-items: center;
    padding-top: 110px;
  }
  .manager-row {
    display: flex; align-items: stretch; gap: 28px;
  }
  .manager { text-align: right; padding-top: 8px; }
  .manager-name {
    font-family: "Oswald", sans-serif; font-weight: 600;
    font-size: 36px; color: var(--brand-blue); text-transform: uppercase;
    letter-spacing: .5px; line-height: 1.1; white-space: nowrap;
  }
  .manager-title { font-size: 18px; letter-spacing: 1px; margin-top: 6px; }
  .divider { width: 2px; background: var(--brand-blue); }
  .contact-list { list-style: none; }
  .contact-list li {
    display: flex; align-items: center; gap: 14px;
    font-size: 16px; letter-spacing: .8px; height: 26px; white-space: nowrap;
  }
  .contact-list svg { width: 16px; height: 16px; fill: var(--brand-blue); flex: none; }
  .property { margin-top: 62px; text-align: center; }
  .property-name {
    font-size: 19px; font-weight: 500; color: var(--brand-blue);
    text-transform: uppercase; letter-spacing: .5px;
  }
  .property-address { font-size: 18px; letter-spacing: 1px; margin-top: 4px; }
</style>
</head>
<body>
<main class="canvas">
  <section class="card card-front">
    <div class="brand-lockup">
      <span class="brand-square"></span>
      <span class="brand-name">Harborview Estates LLC</span>
    </div>
    <p class="front-web">www.<span class="web-accent">harborviewest</span>.com</p>
  </section>

  <section class="card card-back">
    <div class="manager-row">
      <div class="manager">
        <h1 class="manager-name">Marisol Quintero</h1>
        <p class="manager-title">Resident Manager</p>
      </div>
      <span class="divider"></span>
      <ul class="contact-list">
        <li><svg viewBox="0 0 16 16"><path d="M3 1l3 3-1.5 2a9 9 0 0 0 5.5 5.5L12 10l3 3-2 2C7 15 1 9 1 3z"/></svg><span>555-210-4418</span></li>
        <li><svg viewBox="0 0 16 16"><rect x="4" y="1" width="8" height="4"/><rect x="1" y="6" width="14" height="6" rx="1"/><rect x="4" y="10" width="8" height="5"/></svg><span>555-210-4470</span></li>
        <li><svg viewBox="0 0 16 16"><path d="M4 1h8v14H4zM5.5 2.5v9h5v-9z"/></svg><span>555-384-9126</span></li>
        <li><svg viewBox="0 0 16 16"><path d="M1 3h14v10H1zm1.5 1.5L8 9l5.5-4.5"/></svg><span>marisol@harborviewest.com</span></li>
        <li><svg viewBox="0 0 16 16"><path d="M8 1a7 7 0 1 0 0 14A7 7 0 0 0 8 1zm0 1.5c1 1.2 1.6 3 1.7 4.8H6.3C6.4 5.5 7 3.7 8 2.5zM2.6 7.3h2.3c.1-1.7.5-3.2 1.2-4.4A5.5 5.5 0 0 0 2.6 7.3zm0 1.4a5.5 5.5 0 0 0 3.5 4.4c-.7-1.2-1.1-2.7-1.2-4.4zm3.7 0c.1 1.8.7 3.6 1.7 4.8 1-1.2 1.6-3 1.7-4.8zm4.8 0c-.1 1.7-.5 3.2-1.2 4.4a5.5 5.5 0 0 0 3.5-4.4zm2.3-1.4a5.5 5.5 0 0 0-3.5-4.4c.7 1.2 1.1 2.7 1.2 4.4z"/></svg><span>www.<span class="web-accent">harborviewest</span>.com</span></li>
      </ul>
    </div>
    <div class="property">
      <h2 class="property-name">Bayside Court Apartments</h2>
      <p class="property-address">4820 Linden Avenue Fairview, CA 90000</p>
    </div>
  </section>
</main>
</body>
</html>
```